Need Web Design for Business Process Outsourcing Company (Quorvane)

Quorvane is a business process outsourcing company. Need a simple site similar to http://www.tallowbrinkhire.com/ but with a more professional and credible look. New to the process; not sure where to start and comparing my options. Please let me know what my options are if I choose to go with you. Logo is attached for your reference. Please use same colorway

Reason: I want the final product to be coded. Please confirm you will be able to code final design.

Industry/Entity Type

Business

Coding

Coded - Design and coding required

```html
<!DOCTYPE html>
<html lang="en">
<head>
<meta charset="utf-8">
<title>Quorvane – Business Process Outsourcing</title>
<link href="https://fonts.googleapis.com/css2?family=Open+Sans:wght@400;600;700;800&display=swap" rel="stylesheet">
<style>
:root{
  --navy:#0a5a94;
  --deep:#0b568c;
  --bar:#0b5d99;
  --bright:#0c8ad0;
  --footer:#0b80c8;
  --footer-dark:#0a5b90;
  --grey:#f4f4f4;
  --text:#555;
  --white:#fff;
}
*{margin:0;padding:0;box-sizing:border-box}
html,body{width:1200px;height:2799px;overflow:hidden;background:var(--white)}
body{font-family:"Open Sans",Arial,sans-serif;color:var(--text)}
.page{position:relative;width:1200px;height:2799px;overflow:hidden}
.abs{position:absolute}
.backdrop{position:absolute;left:0;top:0}

/* hero */
.hero-photo{position:absolute;left:0;top:0;width:1200px;height:648px;
  background:linear-gradient(120deg,#0b4f8c 0%,#1577c4 45%,#0d5aa0 70%,#083f78 100%)}
.brand{position:absolute;display:flex;align-items:center;gap:14px;color:var(--white);font-weight:700}
.brand-mark{width:40px;height:40px;border:4px solid var(--white)}
.brand--head{left:75px;top:48px;font-size:44px}
.call{position:absolute;right:75px;top:52px;color:var(--white);font-size:27px;font-weight:700;display:flex;align-items:center;gap:14px}
.nav{position:absolute;left:75px;top:136px;width:1050px;height:51px;background:var(--bar);
  display:flex;justify-content:space-around;align-items:center;list-style:none}
.nav li{color:var(--white);font-size:14.5px;font-weight:700;text-transform:uppercase}
.hero-title{position:absolute;left:0;width:1200px;top:320px;text-align:center;color:var(--white);font-size:70px;font-weight:800;letter-spacing:2px}
.hero-sub{position:absolute;left:0;width:1200px;top:406px;text-align:center;color:var(--white);font-size:29px}
.dots{position:absolute;left:568px;top:602px;display:flex;gap:7px}
.dots span{width:11px;height:11px;border-radius:50%;background:var(--white)}
.dots span:first-child{background:transparent;border:2px solid var(--white)}

/* section heads */
.section-title{position:absolute;left:0;width:1200px;text-align:center;color:var(--navy);font-size:33px;font-weight:700}
.section-title--light{color:var(--white)}

.welcome-text{position:absolute;left:80px;width:1040px;top:746px;text-align:center;font-size:15.5px;line-height:27px}
.btn{position:absolute;left:524px;top:879px;width:152px;height:42px;background:var(--bright);color:var(--white);
  font-size:15px;font-weight:700;display:flex;align-items:center;justify-content:center}

/* services */
.service{position:absolute;width:330px;color:var(--white)}
.service h3{font-size:18px;font-weight:700;text-transform:uppercase;margin-bottom:4px}
.service p{font-size:15px;line-height:24px}
.service--left{text-align:right}

/* news */
.news-photo{position:absolute;top:1545px;width:330px;height:202px}
.news-item{position:absolute;top:1765px;width:330px}
.news-item h3{color:var(--bright);font-size:17px;font-weight:700;line-height:26px;margin-bottom:10px}
.news-item p{font-size:14.5px;line-height:26px}

/* why */
.why-icons{position:absolute;left:0;top:2140px}
.why-item{position:absolute;top:2244px;width:330px;text-align:center}
.why-item h3{color:var(--bright);font-size:18px;font-weight:700;text-transform:uppercase;margin-bottom:2px}
.why-item p{font-size:15px;line-height:24px}

/* footer */
.brand--foot{left:75px;top:2478px;font-size:42px}
.foot-about{position:absolute;left:75px;top:2555px;width:320px;color:var(--white);font-size:15px;line-height:26px}
.foot-head{position:absolute;top:2474px;color:var(--white);font-size:18px;font-weight:700;text-transform:uppercase}
.contact{position:absolute;left:450px;top:2508px;color:var(--white);font-size:14.5px;line-height:25px;width:230px}
.contact strong{font-weight:700}
.contact .row{display:flex;align-items:center;gap:12px;margin-top:6px}
.field{position:absolute;background:var(--white);color:#777;font-size:13.5px;padding:8px 12px}
.send{position:absolute;left:1017px;top:2644px;width:108px;height:38px;background:var(--footer-dark);color:var(--white);
  font-size:14px;font-weight:700;display:flex;align-items:center;justify-content:center}
.copyright{position:absolute;left:75px;top:2748px;color:var(--white);font-size:13px}
.social{position:absolute;right:75px;top:2740px;display:flex;gap:21px}
.social span{width:25px;height:25px;background:var(--white);border-radius:3px}
</style>
</head>
<body>
<div class="page">

  <svg class="backdrop" width="1200" height="2799" viewBox="0 0 1200 2799" aria-hidden="true">
    <path d="M0 870 Q600 1050 1200 870 L1200 1495 Q600 1330 0 1495 Z" fill="var(--deep)"/>
    <path d="M0 1940 Q600 2090 1200 1940 L1200 2400 L0 2400 Z" fill="var(--grey)"/>
    <path d="M0 2375 Q600 2515 1200 2375 L1200 2799 L0 2799 Z" fill="var(--footer)"/>
    <rect x="0" y="2715" width="1200" height="84" fill="var(--footer-dark)"/>
  </svg>

  <!-- hero -->
  <div class="hero-photo" role="img" aria-label="Blue-toned photo of business colleagues reviewing documents at a desk"></div>
  <div class="brand brand--head"><span class="brand-mark"></span>Quorvane</div>
  <div class="call">
    <svg width="22" height="22" viewBox="0 0 24 24" aria-hidden="true"><path fill="#fff" d="M6.6 10.8a15.1 15.1 0 0 0 6.6 6.6l2.2-2.2a1 1 0 0 1 1-.25 11.4 11.4 0 0 0 3.6.57 1 1 0 0 1 1 1V20a1 1 0 0 1-1 1A17 17 0 0 1 3 4a1 1 0 0 1 1-1h3.5a1 1 0 0 1 1 1c0 1.25.2 2.45.57 3.57a1 1 0 0 1-.25 1z"/></svg>
    CALL US: 1-800-555-0142
  </div>
  <ul class="nav">
    <li>Home</li><li>Who We Are</li><li>What We Do</li><li>Our Solutions</li><li>Blog</li><li>Latest News</li><li>Careers</li><li>Contact Us</li>
  </ul>
  <h1 class="hero-title">QUORVANE</h1>
  <p class="hero-sub">We are a BPO business process outsourcing company</p>
  <div class="dots"><span></span><span></span><span></span><span></span></div>

  <!-- welcome -->
  <h2 class="section-title" style="top:688px">WELCOME TO QUORVANE</h2>
  <p class="welcome-text">Aliquam molestie, mi et imperdiet euismod, dui purus auctor tellus, et interdum lacus lectus et ante. Sed accumsan sollicitudin sapien, sit amet adipiscing turpis gravida ac. In congue, neque ac lobortis volutpat, libero mauris varius mi, vitae suscipit ipsum ligula vitae risus. Duis aliquam nibh a dui iaculis viverra id a velit. Vivamus egestas risus in magna varius commodo. Sed semper viverra egestas.<br>Etiam pretium porttitor lectus, vel ornare neque porta volutpat.</p>
  <div class="btn">READ MORE</div>

  <!-- services -->
  <h2 class="section-title section-title--light" style="top:1014px">OUR SERVICES</h2>
  <svg class="abs" style="left:400px;top:1060px" width="400" height="300" viewBox="400 1060 400 300" aria-hidden="true">
    <g stroke="#fff" stroke-width="2.5" fill="none">
      <line x1="599" y1="1213" x2="467" y2="1114"/><line x1="599" y1="1213" x2="726" y2="1114"/>
      <line x1="599" y1="1213" x2="435" y2="1205"/><line x1="599" y1="1213" x2="761" y2="1205"/>
      <line x1="599" y1="1213" x2="467" y2="1306"/><line x1="599" y1="1213" x2="730" y2="1306"/>
    </g>
    <g fill="var(--deep)" stroke="#fff" stroke-width="3">
      <circle cx="599" cy="1213" r="88"/>
      <circle cx="467" cy="1114" r="30"/><circle cx="726" cy="1114" r="30"/>
      <circle cx="435" cy="1205" r="30"/><circle cx="761" cy="1205" r="30"/>
      <circle cx="467" cy="1306" r="30"/><circle cx="730" cy="1306" r="30"/>
    </g>
    <circle cx="599" cy="1213" r="26" fill="#fff"/>
    <g fill="#fff">
      <path d="M455 1104h24v15h-14l-6 6v-6h-4z"/>
      <path d="M423 1196h5l4 13h13l3-10h-18" stroke="#fff" stroke-width="3" fill="none"/>
      <circle cx="434" cy="1215" r="2.5"/><circle cx="444" cy="1215" r="2.5"/>
      <path d="M478 1295l3 3-12 13-3-3z"/><circle cx="462" cy="1315" r="4"/>
      <circle cx="719" cy="1106" r="4"/><circle cx="733" cy="1106" r="4"/><circle cx="726" cy="1104" r="4"/>
      <path d="M714 1126v-10h10v10zM728 1126v-10h10v10zM721 1122v-12h10v12z"/>
      <circle cx="761" cy="1200" r="7"/><rect x="757" y="1208" width="8" height="6"/>
      <rect x="719" y="1300" width="22" height="15" rx="2"/><rect x="726" y="1295" width="8" height="5" fill="none" stroke="#fff" stroke-width="2"/>
    </g>
  </svg>
  <div class="service service--left" style="left:75px;top:1072px"><h3>Customer Service</h3><p>Aliquam molestie, mi et imperdiet euismod, dui purus auctor tellus, et interdum</p></div>
  <div class="service service--left" style="left:50px;top:1170px;width:330px"><h3>E-Commerce</h3><p>Aliquam molestie, mi et imperdiet euismod, dui purus auctor tellus</p></div>
  <div class="service service--left" style="left:75px;top:1272px"><h3>Creative</h3><p>Aliquam molestie, mi et imperdiet euismod, dui purus auctor tellus, et interdum</p></div>
  <div class="service" style="left:786px;top:1072px"><h3>Strategy</h3><p>Aliquam molestie, mi et imperdiet euismod, dui purus auctor tellus, et interdum</p></div>
  <div class="service" style="left:821px;top:1170px;width:300px"><h3>IT Solutions</h3><p>Aliquam molestie, mi et imperdiet euismod, dui purus auctor tellus</p></div>
  <div class="service" style="left:786px;top:1272px"><h3>Human Resources</h3><p>Aliquam molestie, mi et imperdiet euismod, dui purus auctor tellus, et interdum</p></div>

  <!-- news -->
  <h2 class="section-title" style="top:1480px">LATEST NEWS</h2>
  <div class="news-photo" style="left:75px;background:linear-gradient(90deg,#1c5fb0,#3d8ad6 55%,#dfe9f3)" role="img" aria-label="Support agent wearing a headset in front of a world map"></div>
  <div class="news-photo" style="left:435px;background:linear-gradient(180deg,#e9eef3,#6f8aa8 60%,#3b5370)" role="img" aria-label="Hands on a keyboard with a glowing network of people icons"></div>
  <div class="news-photo" style="left:795px;background:linear-gradient(160deg,#d9dde2,#8c96a3 55%,#4d5560)" role="img" aria-label="Team meeting in a bright office with an outsourcing banner"></div>
  <div class="news-item" style="left:75px"><h3>Aliquam molestie, mi et imperdiet euismod, dui purus auctor...</h3><p>Sed accumsan sollicitudin sapien, sit amet adipiscing turpis gravida ac. In congue, neque ac lobortis volutpat...</p></div>
  <div class="news-item" style="left:435px"><h3>Aliquam molestie, mi et imperdiet euismod, dui purus auctor...</h3><p>Sed accumsan sollicitudin sapien, sit amet adipiscing turpis gravida ac. In congue, neque ac lobortis volutpat...</p></div>
  <div class="news-item" style="left:795px"><h3>Aliquam molestie, mi et imperdiet euismod, dui purus auctor...</h3><p>Sed accumsan sollicitudin sapien, sit amet adipiscing turpis gravida ac. In congue, neque ac lobortis volutpat...</p></div>

  <!-- why -->
  <h2 class="section-title" style="top:2070px">WHY QUORVANE</h2>
  <svg class="why-icons" width="1200" height="80" viewBox="0 2090 1200 80" aria-hidden="true">
    <g fill="none" stroke="var(--navy)" stroke-width="3">
      <circle cx="240" cy="2127" r="31"/><circle cx="600" cy="2127" r="31"/><circle cx="960" cy="2127" r="31"/>
    </g>
    <g fill="var(--navy)">
      <path d="M231 2113h13l6 6v22h-19z"/>
      <path d="M588 2124h6v15h-6zM596 2124l6-10c3 0 4 2 3 5l-1 4h8c2 0 3 2 2 4l-3 10c-1 2-2 2-4 2h-11z"/>
      <circle cx="960" cy="2118" r="6"/><circle cx="948" cy="2123" r="4.5"/><circle cx="972" cy="2123" r="4.5"/>
      <path d="M950 2139c0-8 4-12 10-12s10 4 10 12zM940 2137c0-5 3-8 7-8l2 8zM980 2137c0-5-3-8-7-8l-2 8z"/>
    </g>
  </svg>
  <div class="why-item" style="left:75px"><h3>Our Facilities</h3><p>Aliquam molestie, mi et imperdiet euismod, dui purus auctor tellus, et interdum</p></div>
  <div class="why-item" style="left:435px"><h3>Success Stories</h3><p>Aliquam molestie, mi et imperdiet euismod, dui purus auctor tellus, et interdum</p></div>
  <div class="why-item" style="left:795px"><h3>Our People</h3><p>Aliquam molestie, mi et imperdiet euismod, dui purus auctor tellus, et interdum</p></div>

  <!-- footer -->
  <div class="brand brand--foot"><span class="brand-mark"></span>Quorvane</div>
  <p class="foot-about">Aliquam molestie, mi et imperdiet euismod, dui purus auctor tellus, et interdum lacus lectus et ante. Sed accumsan sollicitudin sapien, sit amet adipiscing turpis..</p>

  <h4 class="foot-head" style="left:450px">Contact Info</h4>
  <div class="contact">
    <strong>Quorvane</strong><br>412 Harlow Lane,<br>Leeds, LS2 7QT
    <div class="row"><svg width="13" height="13" viewBox="0 0 24 24" aria-hidden="true"><path fill="#fff" d="M6.6 10.8a15.1 15.1 0 0 0 6.6 6.6l2.2-2.2a1 1 0 0 1 1-.25 11.4 11.4 0 0 0 3.6.57 1 1 0 0 1 1 1V20a1 1 0 0 1-1 1A17 17 0 0 1 3 4a1 1 0 0 1 1-1h3.5a1 1 0 0 1 1 1c0 1.25.2 2.45.57 3.57a1 1 0 0 1-.25 1z"/></svg>1-800-555-0142</div>
    <div class="row"><svg width="13" height="11" viewBox="0 0 24 18" aria-hidden="true"><path fill="#fff" d="M0 0h24v2L12 10 0 2zM0 4l12 8 12-8v14H0z"/></svg>info@quorvane.com</div>
  </div>

  <h4 class="foot-head" style="left:703px">Quick Contact</h4>
  <div class="field" style="left:703px;top:2517px;width:206px;height:38px">Name</div>
  <div class="field" style="left:920px;top:2517px;width:205px;height:38px">Email Address</div>
  <div class="field" style="left:703px;top:2566px;width:422px;height:65px">Message</div>
  <div class="send">SEND</div>

  <p class="copyright">Copyright © 2016.Company Name. All Right Reserved</p>
  <div class="social" aria-label="Social links"><span></span><span></span><span></span><span></span><span></span></div>

</div>
</body>
</html>
```